BMR Going Cashless

Hello,
We are a medical office looking to get a flyer created to promote to our patients we will be going "Cashless." Our tagline will be "Cash-Less is Stress-Less"

"Starting in July, to offer you the fastest and most convenient service, we are transitioning to a cashless system. You can now enjoy faster checkout times and greater security with card and contactless payments. More info to come."

I've added two other flyers as sample designs we've used.

Please include logo, addresses, website, phone number

Files to include jpeg, png, pdf (under 5mb), Facebook and Instagram sizing.

Thank you,
Lowen

```html
<!DOCTYPE html>
<html lang="en">
<head>
<meta charset="utf-8">
<title>BMR Foot Care – Cash-Less is Stress-Less</title>
<link href="https://fonts.googleapis.com/css2?family=Bebas+Neue&family=Kaushan+Script&family=Montserrat:ital,wght@0,400;0,500;0,600;0,700;0,800;0,900;1,800&family=Yellowtail&display=block" rel="stylesheet">
<style>
:root{
  --stage:#a8a8a8;
  --teal:#57c2a5;
  --teal-light:#7fd6bd;
  --green:#3f9a72;
  --dark:#2e2e2e;
  --dark-2:#3a3a3a;
  --orange:#f27f4e;
  --white:#ffffff;
  --ink:#2b2b2b;
}
*{margin:0;padding:0;box-sizing:border-box}
html,body{width:1200px;height:2940px;overflow:hidden}
body{background:var(--stage);font-family:"Montserrat",sans-serif;position:relative}
.abs{position:absolute}
.size-label{position:absolute;left:0;width:1200px;text-align:center;font-weight:800;font-size:52px;color:var(--ink);letter-spacing:1px}

/* shared pieces */
.script{font-family:"Yellowtail","Kaushan Script",cursive;line-height:1;white-space:nowrap;overflow:visible}
.condensed{font-family:"Bebas Neue",sans-serif;line-height:1;white-space:nowrap}
.badge{background:var(--orange);color:var(--white);font-weight:700;display:flex;align-items:center;justify-content:center}
.month{font-weight:900;color:var(--white);line-height:1;white-space:nowrap}
.brand{display:flex;align-items:center;gap:12px;color:var(--orange);font-weight:800;white-space:nowrap}
.brand-dot{border-radius:50%;background:var(--teal);flex:none}
.pin{width:18px;height:18px;border-radius:50%;background:var(--orange);position:relative}
.pin::after{content:"";position:absolute;left:6px;top:5px;width:6px;height:6px;border-radius:50%;border:2px solid var(--white)}

/* square post */
.post-square{left:171px;top:179px;width:857px;height:857px;background:var(--dark);overflow:hidden;box-shadow:6px 10px 18px rgba(0,0,0,.35)}
.post-square .script{left:48px;top:40px;width:560px;font-size:140px;color:var(--dark)}
.post-square .condensed{left:51px;top:176px;font-size:122px;color:var(--white)}
.post-square .badge{left:55px;top:279px;width:280px;height:46px;font-size:34px;letter-spacing:7px;border-radius:4px}
.post-square .month{left:55px;top:338px;font-size:92px}
.post-square .intro{left:55px;top:426px;width:430px;font-size:21px;line-height:24px;color:var(--ink);font-weight:500}
.post-square .benefits{left:58px;top:560px;width:480px;font-size:22.5px;line-height:27px;color:var(--white)}
.post-square .benefits b{color:var(--teal);font-weight:700}
.post-square .contactless{left:58px;top:622px;font-size:34px;font-weight:800;font-style:italic;color:var(--orange);white-space:nowrap}
.post-square .more{left:60px;top:670px;font-size:14px;letter-spacing:6px;color:var(--white);font-weight:700}
.post-square .rule{left:46px;top:700px;width:768px;height:2px;background:#777}
.post-square .brand{left:548px;top:620px;font-size:27px}
.post-square .brand-dot{width:22px;height:22px}
.post-square .office{top:724px;width:150px;text-align:center;display:flex;flex-direction:column;align-items:center}
.post-square .office h3{margin-top:6px;font-size:14px;color:var(--teal);font-weight:700}
.post-square .office p{margin-top:4px;font-size:10.5px;line-height:13px;color:var(--white);font-weight:500}
.post-square .divider{top:706px;height:94px;border-left:2px dotted #888}
.post-square .contact-head{left:548px;top:710px;font-size:17px;letter-spacing:5px;color:var(--teal);font-weight:700}
.post-square .phone{left:548px;top:738px;display:flex;align-items:center;gap:10px;font-size:31px;color:var(--white);font-weight:700}
.post-square .web{left:544px;top:785px;width:313px;height:28px;background:var(--orange);color:var(--white);font-size:17px;letter-spacing:4px;padding-left:14px;line-height:28px}

/* story post */
.post-story{left:203px;top:1230px;width:794px;height:1411px;background:var(--dark);overflow:hidden;box-shadow:6px 10px 18px rgba(0,0,0,.35)}
.post-story .brand{left:0;width:794px;justify-content:center;top:72px;font-size:38px}
.post-story .brand-dot{width:30px;height:30px}
.post-story .script{left:0;width:794px;text-align:center;top:225px;font-size:180px;color:var(--teal)}
.post-story .condensed{left:0;width:794px;text-align:center;top:412px;font-size:150px;color:var(--orange)}
.post-story .badge{left:160px;top:593px;width:473px;height:78px;font-size:58px;letter-spacing:14px;border-radius:12px;border:2px solid #f7c0a6}
.post-story .month{left:0;width:794px;text-align:center;top:700px;font-size:108px}
.post-story .intro{left:0;width:794px;text-align:center;top:815px;font-size:27px;line-height:31px;color:var(--ink);font-weight:500}
.post-story .dash{left:42px;top:917px;width:713px;border-top:2px dashed #3c6f5e}
.post-story .enjoy{left:39px;top:942px;font-size:50px;line-height:57px;font-weight:800;color:var(--white)}
.post-story .enjoy span{color:var(--orange)}
.post-story .vline{left:299px;top:951px;height:154px;border-left:2px dotted #3c6f5e}
.post-story .checks{left:335px;top:950px;list-style:none}
.post-story .checks li{display:flex;align-items:center;gap:12px;font-size:27px;font-weight:600;color:var(--ink);height:47px}
.post-story .more{left:337px;top:1097px;font-size:19px;letter-spacing:8px;color:var(--white);font-weight:700}
.post-story .office{top:1168px;width:234px;height:125px;background:var(--dark);border-radius:6px;text-align:center;padding-top:26px}
.post-story .office .pin{position:absolute;left:108px;top:-9px;width:20px;height:20px}
.post-story .office h3{font-size:21px;color:var(--teal);font-weight:700}
.post-story .office p{margin-top:3px;font-size:15.5px;line-height:19px;color:var(--white);font-weight:500}
.post-story .phone{left:42px;top:1327px;display:flex;align-items:center;gap:12px;font-size:41px;color:var(--ink);font-weight:700}
.post-story .web{left:407px;top:1322px;width:400px;height:42px;border:3px solid var(--orange);border-right:none;border-radius:21px 0 0 21px;color:var(--white);font-size:22px;letter-spacing:5px;line-height:36px;padding-left:20px}
</style>
</head>
<body>

<!-- 1080 x 1080 -->
<section class="abs post-square">
  <svg class="abs" style="left:0;top:0" width="857" height="857" viewBox="0 0 857 857">
    <defs>
      <radialGradient id="sq-glow" cx="0.75" cy="0.45" r="0.6">
        <stop offset="0" stop-color="#4a4a4a"/><stop offset="1" stop-color="#2e2e2e"/>
      </radialGradient>
    </defs>
    <rect width="857" height="857" fill="url(#sq-glow)"/>
    <path d="M0,0 H820 C790,300 600,560 240,548 C140,545 60,520 0,490 Z" fill="var(--green)"/>
    <path d="M0,0 H812 C780,290 590,548 240,540 C140,537 60,512 0,482 Z" fill="var(--teal-light)"/>
    <path d="M0,0 H790 C760,280 570,540 240,534 C140,531 60,506 0,476 Z" fill="var(--teal)"/>
  </svg>
  <div class="abs script">Cash-Less</div>
  <div class="abs condensed">IS STRESS-LESS</div>
  <div class="abs badge">STARTING</div>
  <div class="abs month">IN JULY</div>
  <p class="abs intro">To offer you the fastest and most convenient service, we are transitioning to a cashless system</p>
  <p class="abs benefits">Now you can enjoy <b>faster checkout times and greater security with card and</b></p>
  <div class="abs contactless">CONTACTLESS PAYMENTS</div>
  <div class="abs more">MORE INFO TO COME....</div>
  <div class="abs rule"></div>
  <div class="abs brand"><span class="brand-dot"></span>BMR FOOT CARE</div>

  <div class="abs office" style="left:45px"><span class="pin"></span><h3>Northfield Office</h3><p>212 Maple Grove<br>Dr.Suite140 Northfield,<br>MD20010</p></div>
  <div class="abs divider" style="left:194px"></div>
  <div class="abs office" style="left:208px"><span class="pin"></span><h3>Lakeside Office</h3><p>45WellnessWay<br>Lakeside,WV25000</p></div>
  <div class="abs divider" style="left:371px"></div>
  <div class="abs office" style="left:376px"><span class="pin"></span><h3>Millbrook Office</h3><p>2750 Orchard Ridge<br>Blvd.Suite 300<br>Millbrook, MD20020</p></div>

  <div class="abs contact-head">CONTACT US TODAY</div>
  <div class="abs phone">
    <svg width="32" height="32" viewBox="0 0 32 32"><circle cx="16" cy="16" r="15" fill="var(--orange)"/><path d="M11 8c1 0 2 3 2.4 4 .3.8-1.4 1.6-1.2 2.4.6 2 3 4.4 5 5 .8.2 1.6-1.5 2.4-1.2 1 .4 4 1.4 4 2.4 0 1.6-2 3.4-3.6 3.2C13 23.4 8.6 19 8 12.6 7.8 10 9.4 8 11 8z" fill="var(--white)"/></svg>
    (555)014-0192
  </div>
  <div class="abs web">www.<b>bmrfootcare</b>.com</div>
</section>
<div class="size-label" style="top:1090px">1080 X 1080</div>

<!-- 1920 x 1080 -->
<section class="abs post-story">
  <svg class="abs" style="left:0;top:0" width="794" height="1411" viewBox="0 0 794 1411">
    <defs>
      <radialGradient id="st-glow" cx="0.5" cy="0.35" r="0.6">
        <stop offset="0" stop-color="#444"/><stop offset="1" stop-color="#2e2e2e"/>
      </radialGradient>
    </defs>
    <rect width="794" height="1411" fill="url(#st-glow)"/>
    <path d="M0,785 Q397,500 794,785 V1411 H0 Z" fill="var(--green)"/>
    <path d="M0,800 Q397,525 794,800 V1411 H0 Z" fill="var(--teal)"/>
  </svg>
  <div class="abs brand"><span class="brand-dot"></span>BMR FOOT CARE</div>
  <div class="abs script">Cash-Less</div>
  <div class="abs condensed">IS STRESS-LESS</div>
  <div class="abs badge">STARTING</div>
  <div class="abs month">IN JULY</div>
  <p class="abs intro">To offer you the fastest and most convenient service,<br>we are transitioning to a cashless system</p>
  <div class="abs dash"></div>
  <div class="abs enjoy">YOU CAN<br><span>NOW<br>ENJOY</span></div>
  <div class="abs vline"></div>
  <ul class="abs checks">
    <li><svg width="20" height="20" viewBox="0 0 20 20"><circle cx="10" cy="10" r="10" fill="var(--orange)"/><path d="M5.5 10.5l3 3 6-6" stroke="var(--white)" stroke-width="2.2" fill="none"/></svg>Faster checkout times</li>
    <li><svg width="20" height="20" viewBox="0 0 20 20"><circle cx="10" cy="10" r="10" fill="var(--orange)"/><path d="M5.5 10.5l3 3 6-6" stroke="var(--white)" stroke-width="2.2" fill="none"/></svg>Greater security with card</li>
    <li><svg width="20" height="20" viewBox="0 0 20 20"><circle cx="10" cy="10" r="10" fill="var(--orange)"/><path d="M5.5 10.5l3 3 6-6" stroke="var(--white)" stroke-width="2.2" fill="none"/></svg>Contactless payments</li>
  </ul>
  <div class="abs more">MORE INFO TO COME....</div>

  <div class="abs office" style="left:39px"><span class="pin"></span><h3>Northfield Office</h3><p>212 Maple Grove<br>Dr.Suite140 Northfield,<br>MD20010</p></div>
  <div class="abs office" style="left:280px"><span class="pin"></span><h3>Lakeside Office</h3><p>45WellnessWay<br>Lakeside,WV25000</p></div>
  <div class="abs office" style="left:522px"><span class="pin"></span><h3>Millbrook Office</h3><p>2750 Orchard Ridge<br>Blvd.Suite 300 Millbrook,<br>MD20020</p></div>

  <div class="abs phone">
    <svg width="42" height="42" viewBox="0 0 32 32"><circle cx="16" cy="16" r="15" fill="var(--orange)"/><path d="M11 8c1 0 2 3 2.4 4 .3.8-1.4 1.6-1.2 2.4.6 2 3 4.4 5 5 .8.2 1.6-1.5 2.4-1.2 1 .4 4 1.4 4 2.4 0 1.6-2 3.4-3.6 3.2C13 23.4 8.6 19 8 12.6 7.8 10 9.4 8 11 8z" fill="var(--white)"/></svg>
    (555)014-0192
  </div>
  <div class="abs web">www.<b>bmrfootcare</b>.com</div>
</section>
<div class="size-label" style="top:2705px">1920 X 1080</div>

</body>
</html>
```